342BrightVolt Nissan NV-1500 2016 Van Wrap

I own a renewable energy company focused on solar panel sales an installation. I need a van wrap created for my Nissan NV-1500 2016 Van. May add additional vehicles to the fleet. I would like the design to be colorful and eye catching but professional. I would like solar panels to be a large part of the design. The design should fill the van, but not make it over crowded. Include slogan across the back door stating, "Tired of high electric bills? Solar energy is the solution!"

Target Market(s)

Home owner and anyone interesting in renewable energy

Requirements
Must have
• I want my number included (1-877-319-6204) as well as my website url (http://www.342brightvolt.example). The logo attached below also needs to be implemented. I want the colors of the wrap based off of the colors used in the logo.
Professional appearance is needed. Include slogan across the back door stating, "Tired of high electric bills? Solar energy is the solution!"
Nice to have
• Solar panels
Sun
Slogan about solar maybe
Should not have
• Profanities
Inappropriate pictures
Unprofessional appearance.

```html
<!DOCTYPE html>
<html lang="en">
<head>
<meta charset="utf-8">
<title>342BrightVolt Van Wrap</title>
<link rel="stylesheet" href="https://fonts.googleapis.com/css2?family=Montserrat:wght@700&family=Oswald:wght@600&family=Roboto:wght@700&display=swap">
<style>
  :root {
    --wrap-blue: #1f6fb8;
    --wrap-green: #7cba3a;
    --wrap-orange: #e99223;
    --wrap-white: #ffffff;
    --panel-dark: #6a3c12;
    --panel-mid: #9a5a1c;
    --page-bg: #f3f4f6;
    --edge: #d5d8dd;
  }
  * { margin: 0; padding: 0; box-sizing: border-box; }
  html, body { width: 1200px; height: 1200px; overflow: hidden; background: var(--page-bg); }
  .wrap-sheet { position: relative; width: 1200px; height: 1200px; }
  .wrap-panel { position: absolute; display: block; box-shadow: 0 0 0 1px var(--edge); }
  .panel-driver { left: 100px; top: 60px; width: 1000px; height: 340px; }
  .panel-passenger { left: 100px; top: 450px; width: 1000px; height: 340px; }
  .panel-rear { left: 170px; top: 850px; width: 380px; height: 300px; }
  .panel-front { left: 650px; top: 850px; width: 380px; height: 300px; }
  .wordmark { font-family: "Montserrat", sans-serif; font-weight: 700; fill: var(--wrap-blue); }
  .phone { font-family: "Oswald", sans-serif; font-weight: 600; }
  .site { font-family: "Roboto", sans-serif; font-weight: 700; }
  .slogan { font-family: "Oswald", sans-serif; font-weight: 600; fill: var(--wrap-white); letter-spacing: 0.3px; }
</style>
</head>
<body>
<main class="wrap-sheet">

  <!-- Driver side -->
  <svg class="wrap-panel panel-driver" viewBox="0 0 1000 340" aria-label="Driver side wrap">
    <defs>
      <linearGradient id="panelGradA" x1="0" y1="0" x2="0" y2="1">
        <stop offset="0" stop-color="#9a5a1c"/>
        <stop offset="1" stop-color="#6a3c12"/>
      </linearGradient>
    </defs>
    <rect class="base" width="1000" height="340" fill="var(--wrap-white)"/>
    <polygon class="top-sweep" points="0,0 640,0 560,100 360,135 0,200" fill="var(--wrap-blue)"/>
    <polygon class="green-line" points="0,200 360,135 560,100 640,0 670,0 585,118 360,150 0,215" fill="var(--wrap-green)"/>
    <polygon class="orange-base" points="0,265 1000,200 1000,340 0,340" fill="var(--wrap-orange)"/>
    <polygon class="solar-field" role="img" aria-label="Solar panel array texture" points="190,280 700,248 700,340 190,340" fill="url(#panelGradA)"/>
    <polygon class="slogan-band" points="180,255 1000,196 1000,222 180,282" fill="var(--wrap-blue)"/>
    <text class="slogan" x="200" y="274" font-size="17" transform="rotate(-4 200 274)">TIRED OF HIGH ELECTRIC BILLS? SOLAR ENERGY IS THE SOLUTION!</text>
    <text class="wordmark" x="270" y="222" font-size="50" transform="rotate(-4 270 222)">342 BRIGHTVOLT</text>
    <text class="phone" x="330" y="82" font-size="30" fill="var(--wrap-white)" transform="rotate(-4 330 82)">1-877-319-6204</text>
    <text class="site" x="332" y="108" font-size="15" fill="var(--wrap-white)" transform="rotate(-4 332 108)">www.342brightvolt.example</text>
    <circle class="brand-dot" cx="820" cy="90" r="42" fill="var(--wrap-green)"/>
  </svg>

  <!-- Passenger side -->
  <svg class="wrap-panel panel-passenger" viewBox="0 0 1000 340" aria-label="Passenger side wrap">
    <defs>
      <linearGradient id="panelGradB" x1="0" y1="0" x2="0" y2="1">
        <stop offset="0" stop-color="#9a5a1c"/>
        <stop offset="1" stop-color="#6a3c12"/>
      </linearGradient>
    </defs>
    <rect class="base" width="1000" height="340" fill="var(--wrap-white)"/>
    <g class="mirrored-shapes" transform="translate(1000 0) scale(-1 1)">
      <polygon class="top-sweep" points="0,0 640,0 560,100 360,135 0,200" fill="var(--wrap-blue)"/>
      <polygon class="green-line" points="0,200 360,135 560,100 640,0 670,0 585,118 360,150 0,215" fill="var(--wrap-green)"/>
      <polygon class="orange-base" points="0,265 1000,200 1000,340 0,340" fill="var(--wrap-orange)"/>
      <polygon class="solar-field" role="img" aria-label="Solar panel array texture" points="190,280 700,248 700,340 190,340" fill="url(#panelGradB)"/>
      <polygon class="slogan-band" points="180,255 1000,196 1000,222 180,282" fill="var(--wrap-blue)"/>
    </g>
    <text class="slogan" x="130" y="226" font-size="17" transform="rotate(4 130 226)">TIRED OF HIGH ELECTRIC BILLS? SOLAR ENERGY IS THE SOLUTION!</text>
    <text class="wordmark" x="160" y="190" font-size="50" transform="rotate(4 160 190)">342 BRIGHTVOLT</text>
    <text class="phone" x="480" y="52" font-size="30" fill="var(--wrap-white)" transform="rotate(4 480 52)">1-877-319-6204</text>
    <text class="site" x="482" y="78" font-size="15" fill="var(--wrap-white)" transform="rotate(4 482 78)">www.342brightvolt.example</text>
    <circle class="brand-dot" cx="140" cy="80" r="42" fill="var(--wrap-green)"/>
  </svg>

  <!-- Rear doors -->
  <svg class="wrap-panel panel-rear" viewBox="0 0 380 300" aria-label="Rear door wrap">
    <defs>
      <linearGradient id="panelGradC" x1="0" y1="0" x2="0" y2="1">
        <stop offset="0" stop-color="#9a5a1c"/>
        <stop offset="1" stop-color="#6a3c12"/>
      </linearGradient>
    </defs>
    <rect class="base" width="380" height="300" fill="var(--wrap-white)"/>
    <rect class="top-trim" width="380" height="8" fill="var(--wrap-blue)"/>
    <rect class="top-trim-green" y="8" width="380" height="4" fill="var(--wrap-green)"/>
    <rect class="orange-base" y="190" width="380" height="110" fill="var(--wrap-orange)"/>
    <rect class="solar-field" role="img" aria-label="Solar panel array texture" x="0" y="212" width="190" height="88" fill="url(#panelGradC)" opacity="0.85"/>
    <rect class="slogan-band" y="196" width="380" height="22" fill="var(--wrap-blue)"/>
    <text class="slogan" x="190" y="212" font-size="12" text-anchor="middle">TIRED OF HIGH ELECTRIC BILLS? SOLAR ENERGY IS THE SOLUTION!</text>
    <circle class="brand-dot" cx="190" cy="60" r="32" fill="var(--wrap-green)"/>
    <text class="wordmark" x="190" y="130" font-size="28" text-anchor="middle">342 BRIGHTVOLT</text>
    <text class="phone" x="190" y="160" font-size="18" text-anchor="middle" fill="var(--wrap-blue)">1-877-319-6204</text>
    <text class="site" x="190" y="177" font-size="10" text-anchor="middle" fill="var(--wrap-blue)">www.342brightvolt.example</text>
  </svg>

  <!-- Front / hood -->
  <svg class="wrap-panel panel-front" viewBox="0 0 380 300" aria-label="Front hood wrap">
    <rect class="base" width="380" height="300" fill="var(--wrap-white)"/>
    <polygon class="side-blue-left" points="0,0 70,0 70,300 0,300" fill="var(--wrap-blue)"/>
    <polygon class="side-blue-right" points="310,0 380,0 380,300 310,300" fill="var(--wrap-blue)"/>
    <polygon class="green-left" points="70,0 84,0 84,300 70,300" fill="var(--wrap-green)"/>
    <polygon class="green-right" points="296,0 310,0 310,300 296,300" fill="var(--wrap-green)"/>
    <rect class="hood-top" x="84" y="0" width="212" height="60" fill="var(--wrap-blue)"/>
    <circle class="brand-dot" cx="190" cy="112" r="24" fill="var(--wrap-green)"/>
    <text class="wordmark" x="190" y="172" font-size="22" text-anchor="middle">342 BRIGHTVOLT</text>
  </svg>

</main>
</body>
</html>
```